Business Card for Multi-Brand Sportswear Company

We are looking for a business card which represents our company and the multiple brands within it.

The company: Fen Athletics (LTD)
The brands: Fen, TavaPuni, ElmStretch, Grit and Rain

Employees using these cards would be representing Fen Athletics, rather than any of the individual brands. You will see a current design within the uploaded files, to give some inspiration. The actual text of the brands is not necessary, but the logos should be on there is some format.

Our creative minds on this are stretched, so we are looking for someone to make this their own, and show us what a good business card should look like.

We may like to get these printed with spot gloss, so keep that in mind with your designs.

www.fenathletics.co.uk

Industry/Entity Type

Business

Contact Information for Business Card

Leo Pemberton-Hale
Operations Manager
(+44) 1632 960 418
Leo@fenathletics.co.uk
www.fenathletics.co.uk

Font styles to use
Sans Serif
Other font styles liked:
• Eurostile

Colors
ffffff

Requirements
Nice to have
• Dark (black) background

```html
<!DOCTYPE html>
<html lang="en">
<head>
<meta charset="utf-8">
<title>Fen Athletics – Business Card</title>
<link href="https://fonts.googleapis.com/css2?family=Michroma&family=Oswald:wght@500&family=Open+Sans:wght@400;700&display=swap" rel="stylesheet">
<style>
  :root {
    --stage: #1c1c1c;
    --card-dark: #5b5b5d;
    --card-dark-edge: #4e4e50;
    --card-light: #ffffff;
    --ink: #1a1a1a;
    --ink-soft: #555555;
    --accent: #e02a2a;
    --brand-purple: #5e4a6e;
    --brand-grey: #8a8a8c;
    --divider: #b8b8b8;
    --white: #ffffff;
  }
  * { margin: 0; padding: 0; box-sizing: border-box; }
  html, body {
    width: 1200px; height: 1000px; overflow: hidden;
    background: var(--stage);
  }
  .canvas { position: relative; width: 1200px; height: 1000px; }

  .card {
    position: absolute; width: 560px; height: 320px;
    border-radius: 30px; overflow: hidden;
  }

  /* Front: dark brand card */
  .card--front {
    left: 120px; top: 140px;
    background: linear-gradient(160deg, var(--card-dark) 0%, var(--card-dark-edge) 100%);
  }
  .front__watermark {
    position: absolute; left: 40px; top: 70px;
    font-family: "Michroma", sans-serif; font-size: 190px;
    color: rgba(255,255,255,0.07); letter-spacing: 6px; line-height: 1;
  }
  .front__wordmark {
    position: absolute; left: 0; right: 0; top: 110px; text-align: center;
    font-family: "Michroma", sans-serif; font-size: 40px;
    color: var(--white); letter-spacing: 2px;
  }
  .front__tagline {
    position: absolute; left: 0; right: 0; top: 168px; text-align: center;
    font-family: "Michroma", sans-serif; font-size: 14px;
    color: var(--white); letter-spacing: 5px;
  }
  .brand-row {
    position: absolute; left: 50px; right: 50px; bottom: 36px;
    display: flex; justify-content: space-between; align-items: center;
  }
  .brand-badge { width: 36px; height: 36px; }
  .brand-badge--red { border: 3px solid var(--accent); border-radius: 6px; }
  .brand-badge--circle { border: 3px solid var(--brand-grey); border-radius: 50%; }
  .brand-badge--white { background: var(--white); border-radius: 4px; width: 30px; height: 30px; }
  .brand-badge--purple { background: var(--brand-purple); width: 50px; height: 32px; }

  /* Back: white contact card */
  .card--back {
    left: 520px; top: 540px;
    background: var(--card-light);
  }
  .back__logo {
    position: absolute; left: 40px; top: 138px;
    display: flex; align-items: center; gap: 12px;
  }
  .back__logo-dot { width: 16px; height: 16px; background: var(--accent); }
  .back__logo-name {
    font-family: "Michroma", sans-serif; font-size: 22px; color: var(--ink);
  }
  .back__divider {
    position: absolute; left: 286px; top: 40px; width: 1px; height: 240px;
    background: linear-gradient(to bottom, transparent, var(--divider), transparent);
  }
  .contact { position: absolute; left: 310px; top: 56px; width: 230px; }
  .contact__name {
    font-family: "Oswald", sans-serif; font-weight: 500; font-size: 26px;
    letter-spacing: 1.5px; color: var(--ink); line-height: 1.1;
  }
  .contact__name-last { color: var(--accent); }
  .contact__role {
    font-family: "Open Sans", sans-serif; font-weight: 700; font-size: 12px;
    color: var(--ink); margin-top: 2px;
  }
  .contact__address {
    font-family: "Open Sans", sans-serif; font-size: 13px; color: var(--ink-soft);
    margin-top: 14px; line-height: 1.35;
  }
  .contact__list { list-style: none; margin-top: 10px; }
  .contact__item {
    display: flex; align-items: center; gap: 10px;
    font-family: "Open Sans", sans-serif; font-size: 13px; color: var(--ink-soft);
    line-height: 1.55;
  }
  .contact__icon { width: 11px; height: 11px; fill: var(--accent); flex: none; }
  .contact__domain { color: var(--accent); }
</style>
</head>
<body>
<main class="canvas">

  <section class="card card--front" aria-label="Business card front">
    <div class="front__watermark" aria-hidden="true">Fen</div>
    <div class="front__wordmark">FEN ATHLETICS</div>
    <div class="front__tagline">PERFORMANCE WEAR</div>
    <div class="brand-row" aria-label="Group brands">
      <div class="brand-badge brand-badge--red" role="img" aria-label="Grit and Rain brand mark"></div>
      <div class="brand-badge brand-badge--circle" role="img" aria-label="ElmStretch brand mark"></div>
      <div class="brand-badge brand-badge--white" role="img" aria-label="Fen brand mark"></div>
      <div class="brand-badge brand-badge--purple" role="img" aria-label="TavaPuni brand mark"></div>
    </div>
  </section>

  <section class="card card--back" aria-label="Business card back">
    <div class="back__logo">
      <span class="back__logo-dot"></span>
      <span class="back__logo-name">Fen Athletics</span>
    </div>
    <div class="back__divider"></div>
    <div class="contact">
      <div class="contact__name">OWEN <span class="contact__name-last">HARTLEY</span></div>
      <div class="contact__role">Managing Director</div>
      <div class="contact__address">Low Fold, Ashby,<br>Kelsey, KL47QD</div>
      <ul class="contact__list">
        <li class="contact__item">
          <svg class="contact__icon" viewBox="0 0 24 24"><path d="M6.6 10.8a15.1 15.1 0 0 0 6.6 6.6l2.2-2.2c.3-.3.7-.4 1-.2 1.1.4 2.3.6 3.6.6.6 0 1 .4 1 1V20c0 .6-.4 1-1 1A17 17 0 0 1 3 4c0-.6.4-1 1-1h3.5c.6 0 1 .4 1 1 0 1.3.2 2.5.6 3.6.1.3 0 .7-.2 1z"/></svg>
          +44(0)1632 960418
        </li>
        <li class="contact__item">
          <svg class="contact__icon" viewBox="0 0 24 24"><path d="M2 5h20v14H2zM4 7v.5l8 5 8-5V7z"/></svg>
          owen@fenathletics.co.uk
        </li>
        <li class="contact__item">
          <svg class="contact__icon" viewBox="0 0 24 24"><circle cx="12" cy="12" r="10"/></svg>
          <span>www.<span class="contact__domain">fenathletics</span>.co.uk</span>
        </li>
      </ul>
    </div>
  </section>

</main>
</body>
</html>
```